Brightmoor Essentials colloidal silver spray for pets.

We need a label for an 8-oz cobalt blue spray bottle. We are a small company just starting to share the benefits of colloidal silver. Our first offering will be the 8-oz spray bottle for pets. We would also like to update our logo. The finished project should be crisp and incorporate a dog on the label. I have attached the information we would like on the label and our logo, which can be changed to match your vision.
Updates

Hi, I would like to remind you that we are using a cobalt blue bottle with a black sprayer and would like an updated logo. Also, for the business cards, we don't want an animal on them, as we are planning future products for people. thank you

```html
<!DOCTYPE html>
<html lang="en">
<head>
<meta charset="utf-8">
<title>Brightmoor Essentials – Colloidal Silver Spray Label</title>
<link href="https://fonts.googleapis.com/css2?family=Hind:wght@600;700&family=Montserrat:wght@800&family=Rye&display=swap" rel="stylesheet">
<style>
  :root {
    --canvas: #ececec;
    --sky-top: #eaf7fd;
    --sky-bottom: #31b4ea;
    --navy: #2e3192;
    --ink-blue: #1f2a8a;
    --green: #13984a;
    --orange: #f47a1f;
    --white: #ffffff;
    --dog-tan: #f2b27c;
    --dog-cream: #f5ead8;
  }
  * { margin: 0; padding: 0; box-sizing: border-box; }
  html, body { width: 1200px; height: 1200px; overflow: hidden; background: var(--canvas); }
  .label {
    position: absolute; left: 360px; top: 98px;
    width: 480px; height: 1004px;
    background: linear-gradient(to bottom, var(--sky-top) 0%, #a9def6 40%, var(--sky-bottom) 84%);
    overflow: hidden;
  }
  .label__titles { position: absolute; inset: 0; }
  .tagline { font-family: "Montserrat", sans-serif; font-weight: 800; fill: var(--ink-blue); }
  .product-name { font-family: "Rye", serif; fill: var(--green); }
  .brand {
    position: absolute; left: 295px; top: 30px; width: 120px; height: 110px;
    display: flex; flex-direction: column; align-items: center; justify-content: center; gap: 6px;
    font-family: "Hind", sans-serif; font-weight: 600; color: var(--navy);
    font-size: 15px; line-height: 1.05; text-align: center;
  }
  .brand__mark { width: 16px; height: 16px; border-radius: 50%; background: var(--green); }
  .claims {
    position: absolute; left: 255px; top: 174px; width: 200px;
    font-family: "Hind", sans-serif; font-weight: 700; color: var(--navy);
    font-size: 21px; line-height: 25px; text-align: center;
  }
  .origin-badge {
    position: absolute; left: 303px; top: 296px; width: 104px; height: 104px;
    border-radius: 50%; background: var(--white); border: 3px solid #c9c9c9;
  }
  .dog-art {
    position: absolute; left: 243px; top: 433px; width: 215px; height: 335px;
    background: linear-gradient(to bottom, var(--dog-tan) 0%, var(--dog-cream) 60%, var(--dog-tan) 100%);
    border-radius: 90px 90px 30px 30px; opacity: .85;
  }
  .audience {
    position: absolute; left: 236px; top: 780px; width: 220px; text-align: center;
    font-family: "Montserrat", sans-serif; font-weight: 800; font-size: 34px; color: var(--orange);
  }
  .info-band {
    position: absolute; left: 0; bottom: 0; width: 100%; height: 156px;
    background: var(--navy); color: var(--white); font-family: "Hind", sans-serif; font-weight: 700;
  }
  .net-weight { position: absolute; left: 22px; top: 22px; width: 104px; text-align: center; }
  .net-weight__caption { font-size: 17px; line-height: 20px; }
  .net-weight__value { font-size: 29px; line-height: 28px; }
  .benefits {
    position: absolute; right: 22px; top: 24px; text-align: right;
    font-size: 21px; line-height: 26px;
  }
</style>
</head>
<body>
  <main class="label">
    <svg class="label__titles" width="480" height="1004" viewBox="0 0 480 1004">
      <text class="tagline" transform="translate(73,818) rotate(-90)" font-size="38" textLength="615" lengthAdjust="spacingAndGlyphs">NATURAL FIRST AID FOR PETS</text>
      <text class="product-name" transform="translate(203,818) rotate(-90)" font-size="132" textLength="790" lengthAdjust="spacingAndGlyphs">COLLOIDAL SILVER</text>
    </svg>

    <div class="brand">
      <span class="brand__mark"></span>
      <span>Brightmoor<br>Essentials</span>
    </div>

    <div class="claims">10 PPM<br>No Preservaties<br>100% Pure<br>No Additives</div>

    <div class="origin-badge"></div>

    <div class="dog-art" role="img" aria-label="Illustration of a smiling beagle puppy sitting, wearing a pink collar"></div>

    <div class="audience">FOR DOGS</div>

    <section class="info-band">
      <div class="net-weight">
        <div class="net-weight__caption">Net Wt:</div>
        <div class="net-weight__value">500ml<br>8 OZ</div>
      </div>
      <div class="benefits">
        Anti microbial, Anti Fungal<br>
        Anti Bacterial, Anti Viral<br>
        Treats burns, Bites, Cuts<br>
        Abrasions, Hots Spots
      </div>
    </section>
  </main>
</body>
</html>
```